FREE BBQ for life if you win our business with your creative menu design

Looking for a 11x17 size menu. we are a full service BBQ restaurant. We have an upscale environment as well as up scale service. We offer 5 star dinning at a casual price. we are on route 84 and are proud of that. we offer the finest smoked meats. Specializing in smoked pork beef and bison. we have an old barn wood decor. we only use oak to smoke our meats. use a lot of tarnished metal as well as some string nail art. Looking for a menu that goes along our style. i have attached as many pictures as i could to give you a fill of how we do it out here.
PLEASE USE THE 11"X17" MENU TEMPLATE ATTACHED IN THE PROJECT BRIEF.
Target Market(s)
Cool people and there families.
Industry/Entity Type
Business
Requirements
Must have
- I have attached the Current menu we use. File brantlys menu pub. Those are all the Items. There will be some changes as we but together the new menu. The prices are changing. but that should be an easy change as we go.
Nice to have
- We are getting away from the lunch dinner menu and going to an all day menu. so rather than coming with toast or bun we will now be asking as an option. I have attached a menu i tried to make as a sample of how we will be doing it. new menu single page and new menu single page flame. These are ideas i had but could not really make it work. so use them as an idea of what we are looking for but be creative.

```html
<!DOCTYPE html>
<html lang="en">
<head>
<meta charset="utf-8">
<title>Brantlys Barbeque – Menu</title>
<link rel="stylesheet" href="https://fonts.googleapis.com/css2?family=Alfa+Slab+One&family=Arvo:wght@700&family=Open+Sans:wght@400&display=swap">
<style>
  :root{
    --page-bg:#d4d5d7;
    --ink-black:#161616;
    --panel-dark:#1e1d1c;
    --panel-light:#ffffff;
    --flame:#e5562b;
    --star-blue:#1f6fd1;
    --name-dark:#2b1f19;
    --desc-red:#8a3a1c;
    --name-tan:#d8bd85;
    --desc-amber:#c9763a;
    --intro-light:#b9b4ac;
    --intro-dark:#3b3531;
  }
  *{box-sizing:border-box;margin:0;padding:0}
  html,body{width:935px;height:1200px;overflow:hidden;background:var(--page-bg)}
  .menu{
    position:absolute;left:88px;top:20px;width:730px;height:1118px;
    transform:scale(1.038);transform-origin:0 0;
    font-family:"Open Sans",sans-serif;
  }
  .col{position:absolute;top:0;height:1118px}
  .col-left{left:0;width:363px;background:var(--panel-light)}
  .col-left .texture{position:absolute;left:0;top:148px;width:363px;height:970px;
    background:radial-gradient(ellipse at 55% 45%,#e9e9e9 0%,#f4f4f4 45%,#ffffff 80%)}
  .col-right{left:363px;width:367px;background:linear-gradient(180deg,#1a1918 0%,#232120 55%,#1b1a19 100%)}
  .masthead{position:absolute;left:0;top:0;width:363px;height:148px;background:var(--ink-black)}
  .brand{position:absolute;left:48px;top:38px;display:flex;align-items:center;gap:10px}
  .brand-dot{width:30px;height:30px;border-radius:50%;background:var(--star-blue)}
  .brand-name{font-family:"Alfa Slab One",serif;color:var(--flame);font-size:26px;line-height:30px;letter-spacing:.5px}
  .section{position:absolute;width:300px}
  .col-left .section{left:41px}
  .col-right .section{left:28px;width:306px}
  .section-title{display:flex;align-items:center;justify-content:center;gap:22px;height:26px;margin-bottom:10px}
  .section-title h2{font-family:"Alfa Slab One",serif;font-weight:400;font-size:23px;color:var(--flame);letter-spacing:.5px}
  .stars{color:var(--star-blue);font-size:13px;letter-spacing:4px}
  .lead{font-family:"Arvo",serif;font-size:10.5px;margin-bottom:2px}
  .intro{font-size:8.4px;line-height:11px;margin-bottom:11px}
  .item{margin-bottom:12px}
  .item-line{display:flex;align-items:baseline;font-family:"Arvo",serif;font-size:8.6px;line-height:14px;letter-spacing:.3px}
  .leader{flex:1;border-bottom:1.6px dotted currentColor;margin:0 6px 3px 3px;opacity:.85}
  .price{width:26px;text-align:right}
  .desc{font-size:7.6px;line-height:10.3px;width:264px}
  .col-left .lead{color:var(--name-dark)}
  .col-left .intro{color:var(--intro-dark)}
  .col-left .item-line{color:var(--name-dark)}
  .col-left .desc{color:var(--desc-red)}
  .col-right .lead{color:var(--name-tan)}
  .col-right .intro{color:var(--intro-light)}
  .col-right .item-line{color:var(--name-tan)}
  .col-right .desc{color:var(--desc-amber)}
  .photo{position:absolute;left:0;top:1002px;width:367px;height:116px;
    background:linear-gradient(100deg,#2a1a14 0%,#6b3526 35%,#a4584a 55%,#4a2219 80%,#1a1210 100%)}
</style>
</head>
<body>
<main class="menu">
  <section class="col col-left">
    <div class="texture" role="img" aria-label="Faint vintage roadside sign texture"></div>
    <header class="masthead">
      <div class="brand"><span class="brand-dot"></span><span class="brand-name">BRANTLYS<br>BARBEQUE</span></div>
    </header>

    <div class="section" style="top:166px">
      <div class="section-title"><span class="stars">★★★</span><h2>BISON</h2><span class="stars">★★★</span></div>
      <p class="lead">Heart healthy</p>
      <p class="intro">Comes with 1 sides and your choice of Texas toast, Kaiser bun, Whole wheat bread or Glutton Free bread</p>
      <div class="item"><div class="item-line"><span>BISON BRISTEK</span><span class="leader"></span><span class="price">18.65</span></div><p class="desc">The belly of beast, smoked then sliced thin and grilled . Juicy and tender</p></div>
      <div class="item"><div class="item-line"><span>BISON BURGUER</span><span class="leader"></span><span class="price">18.65</span></div><p class="desc">Smoked then grilled served with pepper jack cheese lettuce tomato pickle toped with spicy ranch</p></div>
      <div class="item"><div class="item-line"><span>BISON STEAK</span><span class="leader"></span><span class="price">18.65</span></div><p class="desc">The belly of beast, smoked then sliced thin and grilled . Juicy and tender</p></div>
    </div>

    <div class="section" style="top:402px">
      <div class="section-title"><span class="stars">★★★</span><h2>SMOKED</h2><span class="stars">★★★</span></div>
      <p class="intro">Comes with 1 sides and your choice of Texas toast, Kaiser bun, Whole wheat bread or Glutton Free bread</p>
      <div class="item"><div class="item-line"><span>BABY RACK RIBS FULL RACK</span><span class="leader"></span><span class="price">19.96</span></div><div class="item-line"><span>BABY RACK RIBS HALF RACK</span><span class="leader"></span><span class="price">18.65</span></div><p class="desc">Tender to the bone, finger licking good, never need a knife, best ribs you'll ever have.</p></div>
      <div class="item"><div class="item-line"><span>ST. LOUIS RIBS</span><span class="leader"></span><span class="price">16.45</span></div><p class="desc">A nice big tender spare rib , slow smoked to tender that you can sink your teeth into.</p></div>
      <div class="item"><div class="item-line"><span>BEEF BRISKET</span><span class="leader"></span><span class="price">10.95</span></div><p class="desc">The most insane mouth watering smoky, moist, succulent piece of meat your mouth will ever have</p></div>
      <div class="item"><div class="item-line"><span>PULLED PORK</span><span class="leader"></span><span class="price">9.59</span></div><p class="desc">Smoked for 18-20 hrs. then pulled and mixed with our signature base barbeque sauce</p></div>
      <div class="item"><div class="item-line"><span>SLICED PORK</span><span class="leader"></span><span class="price">9.54</span></div><p class="desc">Smoked juicy tenderloin sliced thin then grilled per order</p></div>
      <div class="item"><div class="item-line"><span>SMOKED TURKEY</span><span class="leader"></span><span class="price">9.54</span></div><p class="desc">Breast meat smoked and sliced. Juicy and tender</p></div>
      <div class="item"><div class="item-line"><span>SMOKED CHICKEN HALF</span><span class="leader"></span><span class="price">9.59</span></div><p class="desc">Moist and juicy smoked Breast and thigh on the bone basted with our signature sauce on the grill</p></div>
      <div class="item"><div class="item-line"><span>RIB EYE</span><span class="leader"></span><span class="price">9.59</span></div><p class="desc">12oz juicy steak grilled to your desired temp</p></div>
    </div>

    <div class="section" style="top:840px">
      <div class="section-title"><span class="stars">★★★</span><h2>WRAPS</h2><span class="stars">★★★</span></div>
      <p class="lead">Design your own Custom wrap</p>
      <p class="intro">Comes with 1 sides and your choice of Texas toast, Kaiser bun, Whole wheat bread or Glutton Free bread</p>
      <div class="item"><div class="item-line"><span>BISON BRISTEK</span><span class="leader"></span><span class="price">18.65</span></div><p class="desc">The belly of beast, smoked then sliced thin and grilled . Juicy and tender</p></div>
      <div class="item"><div class="item-line"><span>BISON BURGUER</span><span class="leader"></span><span class="price">18.65</span></div><p class="desc">Smoked then grilled served with pepper jack cheese lettuce tomato pickle toped with spicy ranch</p></div>
      <div class="item"><div class="item-line"><span>BISON STEAK</span><span class="leader"></span><span class="price">18.65</span></div><p class="desc">The belly of beast, smoked then sliced thin and grilled . Juicy and tender</p></div>
    </div>
  </section>

  <section class="col col-right">
    <div class="section" style="top:44px">
      <div class="section-title"><span class="stars">★★★</span><h2>APPETIZERS</h2><span class="stars">★★★</span></div>
      <p class="lead">Heart healthy</p>
      <p class="intro">Comes with 1 sides and your choice of Texas toast, Kaiser bun, Whole wheat bread or Glutton Free bread</p>
      <div class="item"><div class="item-line"><span>BISON BRISTEK</span><span class="leader"></span><span class="price">18.65</span></div><p class="desc">The belly of beast, smoked then sliced thin and grilled . Juicy and tender</p></div>
      <div class="item"><div class="item-line"><span>BISON BURGUER</span><span class="leader"></span><span class="price">18.65</span></div><p class="desc">Smoked then grilled served with pepper jack cheese lettuce tomato pickle toped with spicy ranch</p></div>
      <div class="item"><div class="item-line"><span>BISON STEAK</span><span class="leader"></span><span class="price">18.65</span></div><p class="desc">The belly of beast, smoked then sliced thin and grilled . Juicy and tender</p></div>
    </div>

    <div class="section" style="top:280px">
      <div class="section-title"><span class="stars">★★★</span><h2>SIDES</h2><span class="stars">★★★</span></div>
      <p class="intro">Comes with 1 sides and your choice of Texas toast, Kaiser bun, Whole wheat bread or Glutton Free bread</p>
      <div class="item"><div class="item-line"><span>BABY RACK RIBS FULL RACK</span><span class="leader"></span><span class="price">19.96</span></div><div class="item-line"><span>BABY RACK RIBS HALF RACK</span><span class="leader"></span><span class="price">18.65</span></div><p class="desc">Tender to the bone, finger licking good, never need a knife, best ribs you'll ever have.</p></div>
      <div class="item"><div class="item-line"><span>ST. LOUIS RIBS</span><span class="leader"></span><span class="price">16.45</span></div><p class="desc">A nice big tender spare rib , slow smoked to tender that you can sink your teeth into.</p></div>
      <div class="item"><div class="item-line"><span>BEEF BRISKET</span><span class="leader"></span><span class="price">10.95</span></div><p class="desc">The most insane mouth watering smoky, moist, succulent piece of meat your mouth will ever have</p></div>
      <div class="item"><div class="item-line"><span>PULLED PORK</span><span class="leader"></span><span class="price">9.59</span></div><p class="desc">Smoked for 18-20 hrs. then pulled and mixed with our signature base barbeque sauce</p></div>
      <div class="item"><div class="item-line"><span>SLICED PORK</span><span class="leader"></span><span class="price">9.54</span></div><p class="desc">Smoked juicy tenderloin sliced thin then grilled per order</p></div>
      <div class="item"><div class="item-line"><span>SMOKED TURKEY</span><span class="leader"></span><span class="price">9.54</span></div><p class="desc">Breast meat smoked and sliced. Juicy and tender</p></div>
      <div class="item"><div class="item-line"><span>SMOKED CHICKEN HALF</span><span class="leader"></span><span class="price">9.59</span></div><p class="desc">Moist and juicy smoked Breast and thigh on the bone basted with our signature sauce on the grill</p></div>
      <div class="item"><div class="item-line"><span>RIB EYE</span><span class="leader"></span><span class="price">9.59</span></div><p class="desc">12oz juicy steak grilled to your desired temp</p></div>
    </div>

    <div class="section" style="top:718px">
      <div class="section-title"><span class="stars">★★★</span><h2>DESSERTS</h2><span class="stars">★★★</span></div>
      <p class="lead">Design your own Custom wrap</p>
      <p class="intro">Comes with 1 sides and your choice of Texas toast, Kaiser bun, Whole wheat bread or Glutton Free bread</p>
      <div class="item"><div class="item-line"><span>BISON BRISTEK</span><span class="leader"></span><span class="price">18.65</span></div><p class="desc">The belly of beast, smoked then sliced thin and grilled . Juicy and tender</p></div>
      <div class="item"><div class="item-line"><span>BISON BURGUER</span><span class="leader"></span><span class="price">18.65</span></div><p class="desc">Smoked then grilled served with pepper jack cheese lettuce tomato pickle toped with spicy ranch</p></div>
      <div class="item"><div class="item-line"><span>BISON STEAK</span><span class="leader"></span><span class="price">18.65</span></div><p class="desc">The belly of beast, smoked then sliced thin and grilled . Juicy and tender</p></div>
    </div>

    <div class="photo" role="img" aria-label="Photo of sliced smoked beef on a dark board"></div>
  </section>
</main>
</body>
</html>
```